Coral Wing Flights brochure

A single A4 brochures that is tri-folded and shows some of our tour packages with contact details.

Please visit www.coralwingflights.com.au to see the designs and images that can be used.

I want to provide designers the freedom to try something creative because I want to give prospective client - normally tourists to Sydney a quality service. I want the brochure to reflect this.

The image on the front page needs to be of the Sydney Harbour. The image MUST be in daylight - not night time.

I have now provided an image of the aircraft (in GIF format). Please use this image and place it over the image of the sydney harbour bridge and quayside concert pavilion.

I may need to discuss this further but what I have not show in the attached files is a small form I will like the client to fill out..

Reservation number
Name
Address
Phone number
Email

We can discuss this at a latter time.

The QR Code needs to contain your web address (www.coralwingflights.com.au)

Target Market(s)

Visitors and tourists to Sydney who want a day trip.
We are providing an exciting way to see Sydney. By air in a light aircraft...

Industry/Entity Type

House

Font styles to use
Sans Serif
Script

Colors
33a6d7
3276b5
85acd3
85cae6
ffffff

Requirements
Must have
• Brochure must be A4 (with about 2 to 3mm bleed - so it can be cut at the printers). They but be folded in 3 to produce a DL size brochure.

The words "Prepare to be amazed" should be in script font...

Please use the following wording for our Terms can conditions...

Terms and Conditions
Coral Wing Flights operates from Merrowdale Airfield within Sydney’s busy airspace Your chosen flight may be subject to delays. Clearance to enter controlled airspace may be refused - this is especially true of our popular Coastline Panorama flight. If this happens, we can either offer other suitable flights, reschedule the flight or, if this isn’t suitable, we provide a refund.
Other aircraft, besides our standard Talbin Skyrunners, are available if we consider they better suit your requirements.
See our web site www.coralwingflights.com.au for full details.
Coral Wing Flights is a trading name of Orvexa Pty Limited
(ABN 81 417 286 309) which operates under the Air Operators Certificate (AOC) of Dorrigan and Welsford Pty Ltd.
Nice to have
• Suggestion - on one of the sides (with the packages) to have a background image.

Suggestion is to keep the brochure light and "airy"

```html
<!DOCTYPE html>
<html lang="en">
<head>
<meta charset="utf-8">
<title>Coral Wing Flights – Tour Packages</title>
<link rel="stylesheet" href="https://fonts.googleapis.com/css2?family=Anton&family=Ubuntu:wght@400;500&display=swap">
<style>
  :root {
    --sky: #33a6d7;
    --royal: #3276b5;
    --navy-line: #2a6aa8;
    --sun: #f6e81a;
    --white: #ffffff;
    --ink: #3276b5;
    --dots: #85acd3;
  }
  * { margin: 0; padding: 0; box-sizing: border-box; }
  html, body { width: 1200px; height: 849px; overflow: hidden; background: var(--white); }
  .panel {
    position: relative; width: 1200px; height: 849px; overflow: hidden;
    font-family: "Ubuntu", "Helvetica Neue", Arial, sans-serif; color: var(--ink);
  }
  .top-band { position: absolute; left: 0; top: 0; width: 1200px; height: 23px; background: var(--sky); }

  .tour { position: absolute; top: 25px; width: 400px; height: 540px; }
  .tour--harbour { left: 0; }
  .tour--coastal { left: 400px; }
  .tour--mountains { left: 800px; }

  .tour__photo { position: absolute; left: 0; top: 0; width: 400px; height: 428px; z-index: 0; }
  .tour--harbour .tour__photo {
    background: linear-gradient(180deg, #8a9aa0 0%, #6f8078 18%, #4f6f69 38%, #3f6462 60%, #5b7b7b 100%);
  }
  .tour--coastal .tour__photo {
    background: linear-gradient(180deg, #5fa3d8 0%, #a9cde8 28%, #c8dcea 40%, #6f8a72 46%, #6a7d5e 56%, #1d3f70 66%, #173766 100%);
  }
  .tour--mountains .tour__photo {
    background: linear-gradient(180deg, #7fa7cc 0%, #c9b9a6 28%, #8c7b67 38%, #9a5f2e 55%, #b06a32 70%, #5a3a20 100%);
  }

  .tour__title {
    position: absolute; left: 0; top: 410px; height: 58px; width: 300px; z-index: 1;
    background: var(--royal); color: var(--sun);
    font-size: 28px; font-weight: 500; line-height: 58px; padding: 4px 0 0 22px; letter-spacing: 0.2px;
  }
  .tour--mountains .tour__title {
    width: 372px; height: 85px; padding: 22px 0 0 22px; line-height: 1;
  }
  .tour__title-small { display: block; font-size: 20px; }
  .tour__title-large { display: block; font-size: 32px; margin-top: 2px; }

  .tour__price {
    position: absolute; left: 20px; top: 366px; z-index: 2;
    display: flex; align-items: baseline; gap: 13px; color: var(--white);
  }
  .tour__amount { font-family: "Anton", "Impact", sans-serif; font-size: 58px; line-height: 1; letter-spacing: 0.5px; }
  .tour__unit { font-size: 24px; }

  .tour__duration {
    position: absolute; top: 472px; left: 60px; width: 240px; height: 34px; z-index: 1;
    background: var(--sky); color: var(--white);
    clip-path: polygon(0 0, 100% 0, 100% 100%, 34px 100%);
    display: flex; align-items: center; gap: 4px; padding-left: 31px;
    font-size: 14.5px; white-space: nowrap;
  }
  .tour--mountains .tour__duration {
    top: 495px; left: 100px; width: 272px; height: 35px; padding-left: 45px;
    clip-path: polygon(0 0, 100% 0, 100% 100%, 35px 100%);
  }

  .stops { position: absolute; list-style: none; }
  .stop {
    position: absolute; white-space: nowrap; font-size: 14px; line-height: 17px;
    padding: 0 0 5px 19px; border-bottom: 1px dotted var(--dots);
  }
  .stop svg { position: absolute; left: 0; top: 2px; }
  .stop--wrap { white-space: normal; }

  .footer {
    position: absolute; left: 0; top: 793px; width: 1200px; height: 56px;
    background: var(--sky); border-top: 4px solid var(--navy-line);
    color: var(--white); font-size: 17px;
  }
  .footer__item { position: absolute; top: 16px; }
  .footer__web--left { left: 83px; }
  .footer__contact { left: 434px; display: flex; align-items: center; gap: 8px; }
  .footer__web--right { left: 887px; }
</style>
</head>
<body>
<main class="panel">
  <div class="top-band"></div>

  <section class="tour tour--harbour">
    <div class="tour__photo" role="img" aria-label="Aerial photo of Sydney Harbour with the city skyline, the concert pavilion on the point and ferries on the water"></div>
    <h2 class="tour__title">SYDNEY HARBOUR</h2>
    <div class="tour__price"><span class="tour__amount">$560</span><span class="tour__unit">per aircraft</span></div>
    <div class="tour__duration">
      <svg width="12" height="12" viewBox="0 0 12 12"><circle cx="6" cy="6" r="5" fill="none" stroke="#fff" stroke-width="1.4"/><path d="M6 3v3h2" fill="none" stroke="#fff" stroke-width="1.2"/></svg>
      <span>Duration: 1 hour 20 mins</span>
    </div>
  </section>

  <section class="tour tour--coastal">
    <div class="tour__photo" role="img" aria-label="Photo of the Sydney coastline with sandstone cliffs, deep blue ocean and a lighthouse on the headland"></div>
    <h2 class="tour__title">SYDNEY COASTAL</h2>
    <div class="tour__price"><span class="tour__amount">$560</span><span class="tour__unit">per aircraft</span></div>
    <div class="tour__duration">
      <svg width="12" height="12" viewBox="0 0 12 12"><circle cx="6" cy="6" r="5" fill="none" stroke="#fff" stroke-width="1.4"/><path d="M6 3v3h2" fill="none" stroke="#fff" stroke-width="1.2"/></svg>
      <span>Duration: 1 hour 20 mins</span>
    </div>
  </section>

  <section class="tour tour--mountains">
    <div class="tour__photo" role="img" aria-label="Photo of the Three Sisters rock formation glowing orange at sunset above the Blue Mountains valley"></div>
    <h2 class="tour__title">
      <span class="tour__title-small">THE BLUE MOUNTAINS, KATOOMBA,</span>
      <span class="tour__title-large">&amp; THE THREE SISTERS</span>
    </h2>
    <div class="tour__price"><span class="tour__amount">$475</span><span class="tour__unit">per aircraft</span></div>
    <div class="tour__duration">
      <svg width="12" height="12" viewBox="0 0 12 12"><circle cx="6" cy="6" r="5" fill="none" stroke="#fff" stroke-width="1.4"/><path d="M6 3v3h2" fill="none" stroke="#fff" stroke-width="1.2"/></svg>
      <span>Duration: 1 hour 20 mins</span>
    </div>
  </section>

  <svg width="0" height="0" style="position:absolute">
    <defs>
      <symbol id="plane" viewBox="0 0 14 14">
        <path d="M13 1 L1 6.2 L5.3 7.6 L6.8 12 L8.4 8.6 L12 11.5 Z" fill="#3276b5"/>
      </symbol>
    </defs>
  </svg>

  <ul class="stops">
    <li class="stop" style="left:20px;top:596px"><svg width="13" height="13"><use href="#plane"/></svg>Parramatta City</li>
    <li class="stop" style="left:20px;top:630px"><svg width="13" height="13"><use href="#plane"/></svg>Hornsby</li>
    <li class="stop" style="left:20px;top:664px"><svg width="13" height="13"><use href="#plane"/></svg>Bahai Temple</li>
    <li class="stop" style="left:20px;top:698px"><svg width="13" height="13"><use href="#plane"/></svg>Sydney Harbour Bridge</li>
    <li class="stop" style="left:252px;top:596px"><svg width="13" height="13"><use href="#plane"/></svg>Opera House</li>
    <li class="stop" style="left:252px;top:630px"><svg width="13" height="13"><use href="#plane"/></svg>Manly</li>
    <li class="stop" style="left:252px;top:664px"><svg width="13" height="13"><use href="#plane"/></svg>Long Reef</li>

    <li class="stop" style="left:415px;top:596px"><svg width="13" height="13"><use href="#plane"/></svg>Cambelltown</li>
    <li class="stop" style="left:415px;top:630px"><svg width="13" height="13"><use href="#plane"/></svg>Stanwell Park</li>
    <li class="stop" style="left:415px;top:664px"><svg width="13" height="13"><use href="#plane"/></svg>Entrance of Port Hacking</li>
    <li class="stop" style="left:415px;top:698px"><svg width="13" height="13"><use href="#plane"/></svg>Entrance of Botany Bay</li>
    <li class="stop stop--wrap" style="left:620px;top:596px;width:178px"><svg width="13" height="13"><use href="#plane"/></svg>Famous Sydney Beaches including Maroubra, Cooge, Bondi &amp; Manly</li>
    <li class="stop" style="left:620px;top:664px"><svg width="13" height="13"><use href="#plane"/></svg>Sydney Heads</li>
    <li class="stop" style="left:620px;top:698px;width:114px"><svg width="13" height="13"><use href="#plane"/></svg>Long Reef</li>

    <li class="stop" style="left:822px;top:630px"><svg width="13" height="13"><use href="#plane"/></svg>Katoomba</li>
    <li class="stop" style="left:822px;top:664px"><svg width="13" height="13"><use href="#plane"/></svg>The Three Sisters</li>
    <li class="stop" style="left:1015px;top:630px"><svg width="13" height="13"><use href="#plane"/></svg>Warragamba Dam</li>
    <li class="stop" style="left:1015px;top:664px"><svg width="13" height="13"><use href="#plane"/></svg>Prospect Resrvour</li>
  </ul>

  <footer class="footer">
    <span class="footer__item footer__web--left">www.coralwingflights.com.au</span>
    <span class="footer__item footer__contact">
      <svg width="14" height="14" viewBox="0 0 14 14"><rect width="14" height="14" rx="3" fill="#fff"/><path d="M4 3.2c.6-.3 1 .1 1.3.7l.5 1.1c.2.5 0 .8-.4 1.1.5 1.1 1.2 1.9 2.3 2.5.3-.4.7-.6 1.1-.4l1.1.5c.6.3.9.8.6 1.3-.4.8-1.2 1.2-2.1.9C6.2 10.1 4.3 8.1 3.5 5.9c-.3-1 .1-2.2.5-2.7z" fill="#33a6d7"/></svg>
      Phone: 1300 418 592 / Fax: (02) 9047-3318
    </span>
    <span class="footer__item footer__web--right">www.coralwingflights.com.au</span>
  </footer>
</main>
</body>
</html>
```